National Mission Critical Construction Contractor needs Stationery Design to make a bold statement

We are a small commercial construction company, working primarily in mission critical facilities across the U.S.. We have exciting corporate changes going an and a new logo and office space so we need new stationery. The final design should incorporate our new logo and invoke a fresh, high-tech feel while looking simple and modern.

Industry/Entity Type

Construction

Contact Information for Business Card

We are required to list our state licensing qualifications on the back of our card.

Font styles to use
Sans Serif

Requirements
Must have
• We need to have a design for second page of stationery, envelopes both standard and with a window and for a 3 x 4 notepad.

```html
<!DOCTYPE html>
<html lang="en">
<head>
<meta charset="utf-8">
<title>Kestrel Bay Stationery</title>
<link href="https://fonts.googleapis.com/css2?family=Questrial&display=swap" rel="stylesheet">
<style>
  :root {
    --brand-blue: #226fb3;
    --brand-navy: #1d5fa3;
    --brand-green: #8cbd2c;
    --paper: #f4f4f4;
    --stage: #d6d6d6;
    --ink: #555b61;
    --faint: #e8e8e8;
  }
  * { margin: 0; padding: 0; box-sizing: border-box; }
  html, body { width: 1200px; height: 1000px; overflow: hidden; }
  body {
    background: var(--stage);
    font-family: "Questrial", "Century Gothic", sans-serif;
    color: var(--ink);
    position: relative;
  }
  .piece {
    position: absolute;
    background: var(--paper);
    overflow: hidden;
    box-shadow: 0 2px 5px rgba(0,0,0,.25);
  }
  .piece svg.art { position: absolute; left: 0; top: 0; }

  .brand { position: absolute; display: flex; align-items: center; gap: 6px; }
  .brand-mark { border: 2px solid var(--brand-navy); border-radius: 50%; flex: none; }
  .brand-name { color: var(--brand-navy); letter-spacing: .01em; line-height: 1; white-space: nowrap; }
  .brand-tag { color: var(--brand-blue); letter-spacing: .16em; text-transform: uppercase; line-height: 1; margin-top: 3px; white-space: nowrap; }

  .small { font-size: 5.6px; line-height: 1.35; color: var(--ink); }
  .contact-block { position: absolute; }
  .contact-line { display: flex; align-items: center; gap: 4px; }
  .contact-line svg { flex: none; }
  .address-rule { border-left: 1.5px solid var(--brand-navy); padding-left: 6px; }

  .letterhead { left: 166px; top: 61px; width: 417px; height: 539px; }
  .second-page { left: 617px; top: 61px; width: 417px; height: 539px; }
  .envelope-front { left: 117px; top: 629px; width: 466px; height: 202px; }
  .envelope-back { left: 616px; top: 629px; width: 466px; height: 202px; }
  .card-front { left: 410px; top: 861px; width: 173px; height: 98px; }
  .card-back { left: 616px; top: 861px; width: 173px; height: 98px; background: var(--brand-blue); }

  .web { position: absolute; font-size: 7.5px; color: var(--ink); }
  .web b { color: var(--brand-navy); font-weight: 400; }
  .card-name { position: absolute; left: 13px; top: 24px; font-size: 6px; color: var(--brand-navy); font-weight: 700; text-transform: uppercase; }
  .card-role { position: absolute; left: 13px; top: 31px; font-size: 4.6px; color: var(--ink); }
</style>
</head>
<body>

<!-- Letterhead -->
<section class="piece letterhead">
  <svg class="art" width="417" height="539" viewBox="0 0 417 539" aria-hidden="true">
    <circle cx="208" cy="470" r="150" fill="none" stroke="var(--faint)" stroke-width="12"/>
    <path d="M0 525 C120 508 260 488 417 498 L417 539 L0 539Z" fill="var(--brand-green)"/>
    <path d="M0 533 C140 514 280 498 417 506 L417 539 L0 539Z" fill="#e2e2e2"/>
    <path d="M130 539 C240 518 340 508 417 515 L417 539Z" fill="var(--brand-blue)"/>
  </svg>
  <div class="brand" style="left:34px;top:37px;">
    <span class="brand-mark" style="width:34px;height:34px;"></span>
    <div>
      <div class="brand-name" style="font-size:17px;">KESTREL BAY</div>
      <div class="brand-tag" style="font-size:4.6px;">Construction Management</div>
    </div>
  </div>
  <div class="contact-block small" style="left:349px;top:37px;transform:translateX(-34px);">
    <div class="address-rule">1280 Harbor Avenue NE<br>Suite 210, Arlington</div>
    <div style="margin-top:5px;padding-left:8px;">
      <div class="contact-line"><svg width="5" height="5" viewBox="0 0 10 10"><path d="M2 0 L4 3 L3 4 C4 6 5 7 6 7 L7 6 L10 8 L8 10 C4 10 0 6 0 2Z" fill="var(--brand-navy)"/></svg>(555) 014-2290</div>
      <div class="contact-line"><svg width="5" height="4" viewBox="0 0 10 8"><rect width="10" height="8" fill="var(--brand-navy)"/><path d="M0 0 L5 4 L10 0" stroke="#fff" fill="none"/></svg>info@kestrelbay.com</div>
      <div class="contact-line"><svg width="5" height="5" viewBox="0 0 10 10"><circle cx="5" cy="5" r="4.3" fill="none" stroke="var(--brand-navy)" stroke-width="1.4"/><path d="M1 5H9M5 1V9" stroke="var(--brand-navy)"/></svg>www.kestrelbay.com</div>
    </div>
  </div>
</section>

<!-- Second page -->
<section class="piece second-page">
  <svg class="art" width="417" height="539" viewBox="0 0 417 539" aria-hidden="true">
    <path d="M0 0 L32 0 C16 90 50 250 45 360 C42 450 22 500 16 539 L0 539Z" fill="var(--brand-green)"/>
    <path d="M0 0 L24 0 C10 90 44 250 40 360 C37 450 18 500 12 539 L0 539Z" fill="#e2e2e2"/>
    <path d="M0 60 C10 150 42 280 38 380 C35 460 18 510 8 539 L0 539Z" fill="var(--brand-blue)"/>
  </svg>
  <div class="brand" style="left:103px;top:75px;">
    <span class="brand-mark" style="width:50px;height:50px;"></span>
    <div>
      <div class="brand-name" style="font-size:23px;">KESTREL BAY</div>
      <div class="brand-tag" style="font-size:6.2px;">Construction Management</div>
    </div>
  </div>
  <div class="web" style="left:173px;top:488px;">www.<b>kestrelbay</b>.com</div>
</section>

<!-- Envelope front -->
<section class="piece envelope-front">
  <svg class="art" width="466" height="202" viewBox="0 0 466 202" aria-hidden="true">
    <circle cx="323" cy="138" r="104" fill="none" stroke="var(--faint)" stroke-width="10"/>
    <path d="M0 182 C140 170 300 155 466 190 L466 202 L0 202Z" fill="var(--brand-green)"/>
    <path d="M0 195 C150 178 310 162 466 194 L466 202 L0 202Z" fill="#e2e2e2"/>
    <path d="M150 202 C260 180 380 168 466 196 L466 202Z" fill="var(--brand-blue)"/>
  </svg>
  <div class="brand" style="left:49px;top:25px;">
    <span class="brand-mark" style="width:34px;height:34px;"></span>
    <div>
      <div class="brand-name" style="font-size:17px;">KESTREL BAY</div>
      <div class="brand-tag" style="font-size:4.6px;">Construction Management</div>
    </div>
  </div>
  <div class="small" style="position:absolute;left:26px;top:162px;">1280 Harbor Avenue NE<br>Suite 210, Arlington</div>
</section>

<!-- Envelope back -->
<section class="piece envelope-back">
  <svg class="art" width="466" height="202" viewBox="0 0 466 202" aria-hidden="true">
    <path d="M0 0 L466 0 L448 66 L18 66Z" fill="var(--brand-blue)"/>
    <circle cx="234" cy="34" r="14" fill="none" stroke="#fff" stroke-width="2"/>
  </svg>
  <div class="small" style="position:absolute;left:0;width:466px;text-align:center;top:173px;">www.kestrelbay.com</div>
</section>

<!-- Business card front -->
<section class="piece card-front">
  <svg class="art" width="173" height="98" viewBox="0 0 173 98" aria-hidden="true">
    <path d="M0 92 C60 86 120 80 173 90 L173 98 L0 98Z" fill="var(--brand-green)"/>
    <path d="M0 96 C60 89 120 83 173 93 L173 98 L0 98Z" fill="#e2e2e2"/>
    <path d="M60 98 C100 89 140 85 173 94 L173 98Z" fill="var(--brand-blue)"/>
  </svg>
  <div class="card-name">Jordan Mercer</div>
  <div class="card-role">General Manager</div>
  <div class="brand" style="left:80px;top:20px;gap:3px;">
    <span class="brand-mark" style="width:19px;height:19px;border-width:1.3px;"></span>
    <div>
      <div class="brand-name" style="font-size:9.5px;">KESTREL BAY</div>
      <div class="brand-tag" style="font-size:2.6px;margin-top:2px;">Construction Management</div>
    </div>
  </div>
  <div class="small" style="position:absolute;left:13px;top:66px;font-size:4.4px;">
    <div>(555) 014-2290</div>
    <div>info@kestrelbay.com</div>
    <div>www.kestrelbay.com</div>
  </div>
  <div class="small" style="position:absolute;right:13px;top:66px;font-size:4.4px;text-align:right;">1280 Harbor Avenue NE<br>Suite 210, Arlington</div>
</section>

<!-- Business card back -->
<section class="piece card-back">
  <svg class="art" width="173" height="98" viewBox="0 0 173 98" aria-hidden="true">
    <circle cx="66" cy="49" r="45" fill="none" stroke="rgba(255,255,255,.1)" stroke-width="4"/>
  </svg>
  <div class="brand" style="left:37px;top:36px;gap:4px;">
    <span class="brand-mark" style="width:22px;height:22px;border-width:1.3px;border-color:#fff;"></span>
    <div>
      <div class="brand-name" style="font-size:10.5px;color:#fff;">KESTREL BAY</div>
      <div class="brand-tag" style="font-size:2.9px;margin-top:2px;color:#fff;">Construction Management</div>
    </div>
  </div>
  <div class="small" style="position:absolute;left:0;width:173px;text-align:center;top:79px;color:#fff;font-size:4.4px;">www.kestrelbay.com</div>
</section>

</body>
</html>
```